Beautify our counselling web application

I have a web application in development and at the moment it is very plain.
It has being developed with laravel and vue. I need a simple design for the user interface to make it look more sleek and professional. I will need someone who is able to code the design as part of the service. The app is very low-cost for voluntary and social enterprise services and we don't have a lot of money so I need someone who is just starting out or someone with a big heart.
I have uploaded current pages to show the contents.
I will tip for good work.

Target Market(s)

Counsellors and psychotherapists

Industry/Entity Type

SaaS

Font styles to use
Serif
Sans Serif

Colors
0054AA
0677BA
7BADD7
CADEEF
E8F1F8

Requirements
Must have
• Ability to code the design into the current site
Nice to have
• elegant, modern. cool, profession. nice examples include merovaultix.com quillbanter.com fenrodu.com
Should not have
• corny literal 90s icons, icons with more than one colour using primary colours

```html
<!DOCTYPE html>
<html lang="en">
<head>
<meta charset="utf-8">
<title>Counselling App – Screens</title>
<link rel="stylesheet" href="https://fonts.googleapis.com/css2?family=Montserrat:wght@400;500;600;700&family=Nunito+Sans:wght@400;600&display=swap">
<style>
:root{
  --primary:#0054AA;
  --mid:#0677BA;
  --sky:#7BADD7;
  --pale:#CADEEF;
  --wash:#E8F1F8;
  --ink:#1d1d22;
  --muted:#8a8f98;
  --row:#ebebeb;
  --white:#ffffff;
}
*{box-sizing:border-box;margin:0;padding:0}
html,body{width:804px;height:1200px;overflow:hidden}
body{background:var(--sky);font-family:"Montserrat",sans-serif;color:var(--ink);position:relative}
.screen{position:absolute;left:23px;width:758px;height:365px;background:var(--white);overflow:hidden}
.screen--caseload{top:22px}
.screen--dashboard{top:415px}
.screen--client{top:803px}
.sidebar{position:absolute;left:0;top:0;width:129px;height:100%;border-right:1px solid #eef0f3}
.brand{position:absolute;left:11px;top:15px;font-size:10px;font-weight:700;color:var(--primary);letter-spacing:.1px}
.nav-title{position:absolute;left:11px;top:67px;font-size:9.6px;font-weight:700;color:var(--primary)}
.nav-chevron{position:absolute;left:116px;top:70px;width:7px;height:5px}
.nav-list{position:absolute;left:11px;top:94px;list-style:none}
.nav-list li{height:23.3px;font-size:9px;color:#2a2a2f}
.nav-list li.active{color:var(--primary)}
.topbar{position:absolute;left:129px;top:0;right:0;height:37px;box-shadow:0 2px 3px rgba(0,0,0,.06)}
.page-title{position:absolute;left:12px;top:10px;font-size:15px;font-weight:600;color:var(--primary);letter-spacing:.2px;white-space:nowrap}
.page-title .crumb{color:var(--sky)}
.search{position:absolute;left:253px;top:8px;width:176px;height:21px;border:1px solid #c9ccd1;border-radius:11px;background:#f1f2f4;font-size:7.3px;color:#444}
.search .filter{position:absolute;left:10px;top:6px}
.search .caret{position:absolute;left:33px;top:8px}
.search .sep{position:absolute;left:47px;top:4px;width:1px;height:12px;background:#777}
.search .field{position:absolute;left:54px;top:5px;color:#555}
.search .glass{position:absolute;right:8px;top:5px;width:10px;height:10px}
.user{position:absolute;top:0;height:37px}
.avatar{position:absolute;top:8px;left:0;width:22px;height:22px;border-radius:50%;background:radial-gradient(circle at 50% 40%,#c9c3bd,#6d7178 70%,#3c4048)}
.user .caret{position:absolute;left:29px;top:17px}
.user .name{position:absolute;left:40px;top:8px;font-size:8px;color:#333;white-space:nowrap}
.user .role{position:absolute;left:41px;top:20px;font-size:6.6px;color:var(--muted);white-space:nowrap}
.user .divider{position:absolute;left:96px;top:11px;width:1px;height:15px;background:#ddd}
.user .icons{position:absolute;left:108px;top:12px;display:flex;gap:3px}
.user .icons svg{width:13px;height:13px}
.screen--caseload .user{left:458px}
.screen--dashboard .user{left:463px}
.screen--client .user{left:458px}

/* caseload table */
.caseload{position:absolute;left:144px;top:55px;width:598px;height:283px;background:var(--row);border-radius:6px;overflow:hidden;font-family:"Nunito Sans",sans-serif}
.caseload__row{display:grid;grid-template-columns:39.5px 43.5px 59px 30px 68px 60px 80.5px 75px 84.5px 1fr;height:38px}
.caseload__head{background:var(--primary);height:36px}
.caseload__head div{color:var(--white);font-size:8.6px;display:flex;align-items:center;padding-left:8px;border-right:1px solid #4d82bf;white-space:nowrap}
.caseload__head div:first-child{padding-left:13px}
.caseload__head div:last-child{border-right:0;padding-left:11px}
.caseload__body .caseload__row{border-bottom:1px solid #f7f7f7}
.caseload__body .caseload__row div{font-size:7.4px;color:#222;display:flex;align-items:center;justify-content:center;border-right:1px solid #f7f7f7;white-space:nowrap}
.caseload__body .caseload__row div:last-child{border-right:0}
.caseload__body .cell-left{justify-content:flex-start!important;padding-left:6px}
.risk-dot{width:10.5px;height:10.5px;border-radius:50%;background:var(--primary)}
.caseload__body .cell-contacts{gap:4px}
.caseload__fill{height:100%}
.caseload__body .lines{position:absolute;left:0;right:0;top:36px;bottom:0;display:grid;grid-template-columns:39.5px 43.5px 59px 30px 68px 60px 80.5px 75px 84.5px 1fr;pointer-events:none}
.caseload__body .lines span{border-right:1px solid #f7f7f7}

/* dashboard */
.welcome{position:absolute;left:145px;top:52px;width:589px;height:34px;border-radius:8px;background:var(--primary);color:var(--white);font-size:15.5px;font-weight:600;display:flex;align-items:center;justify-content:center;letter-spacing:.3px}
.dash-heading{position:absolute;left:149px;font-size:12px;font-weight:500;color:#111}
.dash-note{position:absolute;left:149px;font-size:7px;font-weight:500;color:#111}
.btn-soft{position:absolute;left:149px;top:127px;width:96px;height:22px;border-radius:3px;background:var(--sky);color:#0b2345;font-size:7px;font-weight:600;display:flex;align-items:center;justify-content:center}

/* client page */
.tab{position:absolute;top:59px;height:25px;border-radius:3px;font-size:8.8px;font-weight:600;display:flex;align-items:center;justify-content:center;letter-spacing:.2px}
.tab--filled{background:var(--mid);color:var(--white)}
.tab--outline{border:1.3px solid var(--primary);color:#111}
.episode{position:absolute;left:145px;top:101px;width:585px;height:169px;background:var(--wash);border-radius:8px}
.episode__title{position:absolute;left:11px;top:8px;font-size:12px;font-weight:500}
.episode__started{position:absolute;left:350px;top:7px;font-size:12px;font-weight:600;white-space:nowrap}
.episode__started span{font-size:9px;font-weight:400}
.btn{position:absolute;height:23px;width:108px;border-radius:3px;background:var(--primary);color:var(--white);font-size:9px;font-weight:600;display:flex;align-items:center;justify-content:center}
.btn--end{left:491px;top:7px;width:83px;height:22px;font-size:8px}
</style>
</head>
<body>

<!-- Caseload -->
<section class="screen screen--caseload">
  <aside class="sidebar">
    <div class="brand">COUNSELLING APP</div>
    <div class="nav-title">MANI NAVIGATION</div>
    <svg class="nav-chevron" viewBox="0 0 7 5"><path d="M1 1l2.5 2.5L6 1" fill="none" stroke="#333" stroke-width="1"/></svg>
    <ul class="nav-list">
      <li>Dashboard</li><li class="active">Caseload</li><li>Calendar</li><li>Address Book</li><li>Users</li><li>Services</li><li>Clients</li><li>Audit</li><li>Monitoring</li><li>Templates</li>
    </ul>
  </aside>
  <header class="topbar">
    <h1 class="page-title">CASELODA</h1>
    <div class="search">
      <span class="filter">Filter</span>
      <svg class="caret" width="6" height="4" viewBox="0 0 6 4"><path d="M0 0h6L3 4z" fill="#333"/></svg>
      <span class="sep"></span>
      <span class="field">Search</span>
      <svg class="glass" viewBox="0 0 10 10"><circle cx="4.2" cy="4.2" r="3.2" fill="none" stroke="#111" stroke-width="1.3"/><path d="M6.6 6.6L9.3 9.3" stroke="#111" stroke-width="1.4"/></svg>
    </div>
    <div class="user">
      <div class="avatar" role="img" aria-label="User profile photo"></div>
      <svg class="caret" width="6" height="4" viewBox="0 0 6 4"><path d="M0 0h6L3 4z" fill="#333"/></svg>
      <div class="name">Username</div>
      <div class="role">Counselling App</div>
      <span class="divider"></span>
      <div class="icons">
        <svg viewBox="0 0 13 13"><circle cx="6.5" cy="6.5" r="6.2" fill="#0054AA"/><path d="M4.6 5a2 2 0 1 1 2.7 1.8c-.6.3-.8.6-.8 1.3" fill="none" stroke="#fff" stroke-width="1.4"/><circle cx="6.5" cy="10" r=".9" fill="#fff"/></svg>
        <svg viewBox="0 0 13 13"><circle cx="6.5" cy="3.6" r="3" fill="#0054AA"/><path d="M1 13c0-4 2.4-6 5.5-6S12 9 12 13z" fill="#0054AA"/></svg>
        <svg viewBox="0 0 13 13"><path d="M5 2H2.5a1 1 0 0 0-1 1v7a1 1 0 0 0 1 1H5" fill="none" stroke="#0054AA" stroke-width="1.4"/><path d="M5.5 4.8h3V2.5l4 4-4 4V8.2h-3z" fill="#0054AA"/></svg>
      </div>
    </div>
  </header>

  <div class="caseload">
    <div class="caseload__row caseload__head">
      <div>Risk</div><div>Alerts</div><div>Clients</div><div>ID</div><div>Services</div><div>Therapist</div><div>Date of Refrrral</div><div>First Contact</div><div>Previous Episode</div><div>Contacts</div>
    </div>
    <div class="caseload__body">
      <div class="lines"><span></span><span></span><span></span><span></span><span></span><span></span><span></span><span></span><span></span><span></span></div>
      <div class="caseload__row"><div><span class="risk-dot"></span></div><div></div><div>Owen Calder</div><div>002</div><div>Demo Services 1</div><div>Marek</div><div>05/07/2022</div><div>20/09/2022</div><div></div><div class="cell-contacts"><svg width="4" height="6" viewBox="0 0 4 6"><path d="M0 0l4 3-4 3z" fill="#111"/></svg>Total: 3</div></div>
      <div class="caseload__row"><div><span class="risk-dot"></span></div><div></div><div>Owen Calder</div><div>002</div><div>Demo Services 1</div><div>Marek</div><div>05/07/2022</div><div>20/09/2022</div><div></div><div class="cell-contacts"><svg width="4" height="6" viewBox="0 0 4 6"><path d="M0 0l4 3-4 3z" fill="#111"/></svg>Total: 3</div></div>
      <div class="caseload__row"><div><span class="risk-dot"></span></div><div></div><div>Owen Calder</div><div>002</div><div>Demo Services 1</div><div>Marek</div><div>05/07/2022</div><div>20/09/2022</div><div></div><div class="cell-contacts"><svg width="4" height="6" viewBox="0 0 4 6"><path d="M0 0l4 3-4 3z" fill="#111"/></svg>Total: 3</div></div>
      <div class="caseload__row"><div><span class="risk-dot"></span></div><div></div><div>Owen Calder</div><div>002</div><div>Demo Services 1</div><div>Marek</div><div>05/07/2022</div><div>20/09/2022</div><div></div><div class="cell-contacts"><svg width="4" height="6" viewBox="0 0 4 6"><path d="M0 0l4 3-4 3z" fill="#111"/></svg>Total: 3</div></div>
      <div class="caseload__row"><div><span class="risk-dot"></span></div><div></div><div>Owen Calder</div><div>002</div><div>Demo Services 1</div><div>Marek</div><div>05/07/2022</div><div>20/09/2022</div><div></div><div class="cell-contacts"><svg width="4" height="6" viewBox="0 0 4 6"><path d="M0 0l4 3-4 3z" fill="#111"/></svg>Total: 3</div></div>
      <div class="caseload__row"><div><span class="risk-dot"></span></div><div></div><div>Owen Calder</div><div>002</div><div>Demo Services 1</div><div>Marek</div><div>05/07/2022</div><div>20/09/2022</div><div></div><div class="cell-contacts"><svg width="4" height="6" viewBox="0 0 4 6"><path d="M0 0l4 3-4 3z" fill="#111"/></svg>Total: 3</div></div>
    </div>
  </div>
</section>

<!-- Dashboard -->
<section class="screen screen--dashboard">
  <aside class="sidebar">
    <div class="brand">COUNSELLING APP</div>
    <div class="nav-title">MANI NAVIGATION</div>
    <svg class="nav-chevron" viewBox="0 0 7 5"><path d="M1 1l2.5 2.5L6 1" fill="none" stroke="#333" stroke-width="1"/></svg>
    <ul class="nav-list">
      <li class="active">Dashboard</li><li>Caseload</li><li>Calendar</li><li>Address Book</li><li>Users</li><li>Services</li><li>Clients</li><li>Audit</li><li>Monitoring</li><li>Templates</li>
    </ul>
  </aside>
  <header class="topbar">
    <h1 class="page-title">DASHBOARD</h1>
    <div class="user">
      <div class="avatar" role="img" aria-label="User profile photo"></div>
      <svg class="caret" width="6" height="4" viewBox="0 0 6 4"><path d="M0 0h6L3 4z" fill="#333"/></svg>
      <div class="name">Username</div>
      <div class="role">Counselling App</div>
      <span class="divider"></span>
      <div class="icons">
        <svg viewBox="0 0 13 13"><circle cx="6.5" cy="6.5" r="6.2" fill="#0054AA"/><path d="M4.6 5a2 2 0 1 1 2.7 1.8c-.6.3-.8.6-.8 1.3" fill="none" stroke="#fff" stroke-width="1.4"/><circle cx="6.5" cy="10" r=".9" fill="#fff"/></svg>
        <svg viewBox="0 0 13 13"><circle cx="6.5" cy="3.6" r="3" fill="#0054AA"/><path d="M1 13c0-4 2.4-6 5.5-6S12 9 12 13z" fill="#0054AA"/></svg>
        <svg viewBox="0 0 13 13"><path d="M5 2H2.5a1 1 0 0 0-1 1v7a1 1 0 0 0 1 1H5" fill="none" stroke="#0054AA" stroke-width="1.4"/><path d="M5.5 4.8h3V2.5l4 4-4 4V8.2h-3z" fill="#0054AA"/></svg>
      </div>
    </div>
  </header>

  <div class="welcome">WELCOME TO DEMO</div>
  <h2 class="dash-heading" style="top:100px">NOTIFICATIONS</h2>
  <div class="btn-soft">Create Notification</div>
  <p class="dash-heading" style="top:162px;font-size:10.5px;font-weight:400">NO NOTIFICATIONS</p>
  <h2 class="dash-heading" style="top:183px">TODAY</h2>
  <p class="dash-note" style="top:204px">No Appointments!</p>
  <h2 class="dash-heading" style="top:220px">REVIEWS</h2>
  <p class="dash-note" style="top:241px">No reviews!</p>
</section>

<!-- Client workspace -->
<section class="screen screen--client">
  <aside class="sidebar">
    <div class="brand">COUNSELLING APP</div>
    <div class="nav-title">MANI NAVIGATION</div>
    <svg class="nav-chevron" viewBox="0 0 7 5"><path d="M1 1l2.5 2.5L6 1" fill="none" stroke="#333" stroke-width="1"/></svg>
    <ul class="nav-list">
      <li>Dashboard</li><li class="active">Caseload</li><li>Calendar</li><li>Address Book</li><li>Users</li><li>Services</li><li>Clients</li><li>Audit</li><li>Monitoring</li><li>Templates</li>
    </ul>
  </aside>
  <header class="topbar">
    <h1 class="page-title" style="left:11px"><span class="crumb">CASELODA /</span> OWEN CALDER</h1>
    <div class="user">
      <div class="avatar" role="img" aria-label="User profile photo"></div>
      <svg class="caret" width="6" height="4" viewBox="0 0 6 4"><path d="M0 0h6L3 4z" fill="#333"/></svg>
      <div class="name">Username</div>
      <div class="role">Counselling App</div>
      <span class="divider"></span>
      <div class="icons">
        <svg viewBox="0 0 13 13"><circle cx="6.5" cy="6.5" r="6.2" fill="#0054AA"/><path d="M4.6 5a2 2 0 1 1 2.7 1.8c-.6.3-.8.6-.8 1.3" fill="none" stroke="#fff" stroke-width="1.4"/><circle cx="6.5" cy="10" r=".9" fill="#fff"/></svg>
        <svg viewBox="0 0 13 13"><circle cx="6.5" cy="3.6" r="3" fill="#0054AA"/><path d="M1 13c0-4 2.4-6 5.5-6S12 9 12 13z" fill="#0054AA"/></svg>
        <svg viewBox="0 0 13 13"><path d="M5 2H2.5a1 1 0 0 0-1 1v7a1 1 0 0 0 1 1H5" fill="none" stroke="#0054AA" stroke-width="1.4"/><path d="M5.5 4.8h3V2.5l4 4-4 4V8.2h-3z" fill="#0054AA"/></svg>
      </div>
    </div>
  </header>

  <div class="tab tab--filled" style="left:141.5px;width:93px">WORKSPACE</div>
  <div class="tab tab--filled" style="left:245px;width:135px">CLIENT INFORMATION</div>
  <div class="tab tab--outline" style="left:400px;width:93px">CLIENT RECORD</div>
  <div class="tab tab--outline" style="left:504px;width:118px">CLIENT PROGRESS</div>
  <div class="tab tab--outline" style="left:636px;width:93px">PAYMENTS</div>

  <div class="episode">
    <div class="episode__title">EPISODE 1</div>
    <div class="episode__started">Started: <span>Wed Sep 14 2022</span></div>
    <div class="btn btn--end">END EPISODE</div>

    <div class="btn" style="left:12.5px;top:48px">Session Record</div>
    <div class="btn" style="left:126px;top:48px">Assessment</div>
    <div class="btn" style="left:239px;top:48px">Risk Management</div>
    <div class="btn" style="left:352.5px;top:48px">Treatment Plan</div>
    <div class="btn" style="left:466px;top:48px">Safeguarding</div>

    <div class="btn" style="left:68px;top:86.5px">Consent</div>
    <div class="btn" style="left:182px;top:86.5px">Document</div>
    <div class="btn" style="left:295px;top:86.5px">Non-Clinical Note</div>
    <div class="btn" style="left:408.5px;top:86.5px">Summary</div>

    <div class="btn" style="left:238.5px;top:124px">Timeline</div>
  </div>
</section>

</body>
</html>
```